Covid 19 Exit Strategy one page brochure

I would like to design, and will need URGENT help, a brochure detailing a Covid 19 Exit Strategy plan. This brochure will need to be understood easily and the graphics inside should make it easy for people to understand without reading the entire text. This project is quite urgent and needs to be completed THIS WEEK - by Saturday may 16th at the latest. I am attaching two examples. I will provide the text.

```html
<!DOCTYPE html>
<html lang="en">
<head>
<meta charset="utf-8">
<title>COVID-19 Phased Exit Strategy</title>
<link href="https://fonts.googleapis.com/css2?family=Montserrat:wght@600;700;800&family=Open+Sans:wght@400;600;700&display=swap" rel="stylesheet">
<style>
:root{
  --red:#e5262c;
  --blue:#41a2de;
  --navy:#12325f;
  --navy-deep:#0b2245;
  --white:#ffffff;
  --ink:#111111;
  --canvas:#eef0f2;
  --line:rgba(255,255,255,.85);
}
*{box-sizing:border-box;margin:0;padding:0}
html,body{width:1200px;height:4000px;overflow:hidden;background:var(--canvas)}
body{font-family:"Open Sans",Arial,sans-serif;color:var(--white)}
.brochure{position:absolute;left:270px;top:5px;width:660px;height:3990px;display:flex;flex-direction:column}

/* header */
.masthead{flex:0 0 188px;position:relative;text-align:center;display:flex;flex-direction:column;justify-content:center;
  background:radial-gradient(circle at 12% 30%,#3b5f94 0,transparent 22%),radial-gradient(circle at 88% 75%,#3b5f94 0,transparent 20%),radial-gradient(circle at 70% 10%,#2d4f84 0,transparent 15%),linear-gradient(180deg,var(--navy) 0%,var(--navy-deep) 100%)}
.masthead__art{position:absolute;inset:0}
.masthead h1{position:relative;font-family:"Montserrat",Arial,sans-serif;font-weight:800;font-size:36px;line-height:1.1;letter-spacing:.5px}
.masthead__sub{position:relative;font-family:"Montserrat",Arial,sans-serif;font-weight:800;font-size:33px;color:var(--red);line-height:1.15}
.masthead__credit{position:relative;font-family:"Montserrat",Arial,sans-serif;font-weight:600;font-size:25px;line-height:1.3}

/* intro */
.intro{flex:0 0 425px;background:var(--red);padding:22px 33px 0}
.intro__lead{font-size:8.8px;line-height:1.4;font-weight:600;text-align:justify}
.badge{display:inline-block;background:var(--white);font-family:"Montserrat",Arial,sans-serif;font-weight:800}
.intro__badge-wrap{text-align:center;margin:14px 0 16px}
.intro__badge{color:var(--red);font-size:17px;padding:5px 14px}
.requirements{display:grid;grid-template-columns:1fr 1fr;column-gap:44px}
.requirements__col{display:flex;flex-direction:column;gap:11px;list-style:none}
.req{display:flex;gap:7px;font-size:8.8px;line-height:1.35;font-weight:600;text-align:justify}
.req__num{flex:0 0 15px;height:15px;border-radius:50%;background:var(--white);color:var(--red);font-weight:700;font-size:9px;display:flex;align-items:center;justify-content:center}

/* stages */
.stage{padding:0 33px;display:flex;flex-direction:column}
.stage--one{flex:0 0 1175px;background:var(--blue)}
.stage--two{flex:0 0 1157px;background:var(--red)}
.stage--three{flex:0 0 980px;background:var(--blue)}
.plan-title{margin:26px auto 0;background:var(--white);color:var(--ink);font-family:"Montserrat",Arial,sans-serif;font-weight:800;font-size:18px;padding:9px 10px;width:594px;text-align:center;white-space:nowrap}
.stage__badge-wrap{text-align:center;margin-top:12px}
.stage__badge{font-size:31px;padding:3px 16px;line-height:1.1}
.stage--one .stage__badge,.stage--three .stage__badge{color:var(--blue)}
.stage--two .stage__badge{color:var(--red)}
.stage--two .stage__badge-wrap,.stage--three .stage__badge-wrap{margin-top:18px}
.stage__lead{font-size:8.8px;line-height:1.4;margin-top:16px}
.stage__seq{font-size:11px;font-weight:600;margin:8px 0 10px}

.grid{display:grid;grid-template-columns:repeat(3,1fr);border:1px solid var(--line)}
.stage--one .grid{grid-template-rows:124px 160px 190px 200px 270px}
.stage--two .grid{grid-template-rows:132px 140px 175px 195px 168px 138px}
.stage--three .grid{grid-template-rows:152px 152px 148px 160px 180px}
.cell{border:0.5px solid var(--line);padding:14px 12px 8px;text-align:center;font-size:8.6px;line-height:1.35;display:flex;flex-direction:column;align-items:center;overflow:hidden}
.cell--wide{grid-column:span 3;padding:16px 40px 8px}
.cell--span2{grid-column:span 2;padding:16px 50px 8px}
.icon{flex:0 0 auto;width:38px;height:38px;border:1.5px solid var(--white);border-radius:7px;margin-bottom:10px;display:block}

/* footer */
.footer{flex:0 0 65px;display:grid;grid-template-columns:210px 1fr 1fr;background:var(--red)}
.footer__org{background:var(--white);color:var(--navy);display:flex;align-items:center;gap:8px;padding-left:22px;font-weight:700;font-size:10px}
.footer__org-mark{width:16px;height:16px;background:var(--red)}
.footer__block{padding:14px 14px;font-size:8.5px;line-height:1.45;white-space:nowrap}
.footer__block strong{font-family:"Montserrat",Arial,sans-serif;font-weight:700;display:block;font-size:9.5px}
</style>
</head>
<body>
<main class="brochure">

  <header class="masthead">
    <div class="masthead__art" role="img" aria-label="Soft blue backdrop with blurred virus particles"></div>
    <h1>COVID-19</h1>
    <p class="masthead__sub">PHASED EXIT STRATEGY</p>
    <p class="masthead__credit">Developed by Lena Varga</p>
  </header>

  <section class="intro">
    <p class="intro__lead">Pandemics have, historically, seen their end both medically - via herd immunity or immunizations. And while there are several clinical trials underway for potential Covid-19 vaccines, we are still a long way from deploying an effective vaccine and one that will stand the test of time as the virus changes. Covid-19 pandemic will be considered 'ended' when there are only occasional traces of localized cases that are quickly contained in specific locations. Today and in the absence of an effective vaccine(s) and for the re-opening of the economies and social activities to be successful, it is critical that the following basic conditions be in place before any lockdowns are lifted and before social activities resume:</p>
    <div class="intro__badge-wrap"><span class="badge intro__badge">GENERAL REQUIREMENTS:</span></div>
    <div class="requirements">
      <ul class="requirements__col">
        <li class="req"><span class="req__num">1</span><span>Single digit downward trend of documented cases within the past 14- days.</span></li>
        <li class="req"><span class="req__num">2</span><span>Hospitals and the health care system are capable of treating patients without operating on a crisis mode.</span></li>
        <li class="req"><span class="req__num">3</span><span>Ability to screen and test symptomatic individuals within 24 hours of identification. Increased and sufficient testing capacity, to test at least 50% of all population if necessary within a timeframe of 3 months.</span></li>
        <li class="req"><span class="req__num">4</span><span>Ability to surge ICU capacity on a short notice - 24h.</span></li>
        <li class="req"><span class="req__num">5</span><span>Ability to track and trace infected patients and contacts on a live basis and across the country and ability to react quickly to any unusual trends or spikes.</span></li>
      </ul>
      <ul class="requirements__col">
        <li class="req"><span class="req__num">6</span><span>Plan in place to trigger targeted or full-scale containment in case of sudden outbreaks.</span></li>
        <li class="req"><span class="req__num">7</span><span>Mandatory use of masks (at least surgical grade) for everyone in all public areas and at work. Mandatory use of N95, or equivalent, masks for all healthcare front workers and for all government agencies and authorities that are involved in overseeing the containment activities.</span></li>
        <li class="req"><span class="req__num">8</span><span>Mandatory daily checks of body temperature for everyone at the workplace or entering public areas.</span></li>
        <li class="req"><span class="req__num">9</span><span>Mandatory sanitation in all places - use of disinfection available on a large scale.</span></li>
      </ul>
    </div>
  </section>

  <section class="stage stage--one">
    <h2 class="plan-title">PHASED COVID-19 LOCKDOWN EXIT STRATEGY PLAN</h2>
    <div class="stage__badge-wrap"><span class="badge stage__badge">STAGE : 1</span></div>
    <p class="stage__lead">To enter this stage, additional to the general requirements, the Effective Reproduction Number (Rt) must be less than 1 and the death rate at less than 3%.</p>
    <p class="stage__seq">The economy and social activities can resume in this sequence:</p>
    <div class="grid">
      <div class="cell"><span class="icon" role="img" aria-label="Elderly person icon"></span>Elderly (60+ years old) and vulnerable individuals should continue to self-isolate.</div>
      <div class="cell"><span class="icon" role="img" aria-label="No gatherings icon"></span>No more than 5 people maximum gathering at a time in public areas and at work.</div>
      <div class="cell"><span class="icon" role="img" aria-label="Work from home icon"></span>Work from home should continue whenever and as much as possible.</div>
      <div class="cell"><span class="icon" role="img" aria-label="Social distancing icon"></span>Social distancing should continue to be re-enforced in public areas, at work and in all areas reopened.</div>
      <div class="cell"><span class="icon" role="img" aria-label="No travel icon"></span>Non-essential travel should be minimized between cities and regions (and within cities and regions where covid-19 infections are still a risk)</div>
      <div class="cell"><span class="icon" role="img" aria-label="Large business icon"></span>Large businesses (300 people and more, manufacturing, services, etc.) can reopen progressively. Common areas should remain closed (cafeteria, restaurant, gym, meeting rooms of no more than 5 people).</div>
      <div class="cell"><span class="icon" role="img" aria-label="Small business icon"></span>Small businesses (300 people and less) can reopen as well with the same conditions as large businesses.</div>
      <div class="cell"><span class="icon" role="img" aria-label="Shop icon"></span>Commercial shops can reopen. Shops should control the flow of people in their facilities not to exceed 30% at a time of standard capacity. Shops should provide disinfectant and temperature control at entry.</div>
      <div class="cell"><span class="icon" role="img" aria-label="Pharmacy icon"></span>Pharmacies will continue to be open. However, they must make available disinfectant for use by clients and will continue to comply with social distancing. Pharmacies should limit the number of client/patient in their stores not to exceed 30% of the standard capacity.</div>
      <div class="cell"><span class="icon" role="img" aria-label="Religious site icon"></span>Religious sites can reopen with a maximum capacity of 30% or less. Social distancing and wearing masks is mandatory. Religious sites should organize (volunteers can help) to check body temperature of everyone accessing the site and provide disinfectant at entry.</div>
      <div class="cell"><span class="icon" role="img" aria-label="Hotel icon"></span>Hotels &amp; tourism (museums, etc.) can reopen but must operate at 30% or less capacity. All common areas (restaurants, gyms, swimming pools, conference rooms, etc.) should remain closed.</div>
      <div class="cell"><span class="icon" role="img" aria-label="School closed icon"></span>All schools should remain closed. On-line courses should continue be the preferred method for education.</div>
      <div class="cell"><span class="icon" role="img" aria-label="Transport icon"></span>Transportation (buses, taxis, airlines) will resume progressively. No air travels permitted in and out of Covid-19 known hotspots, locally or internationally. Entry to country should be limited and strictly controlled. All landing passengers and visitors regardless of the country of origin should be tested for Covid-19 at arrival. All passengers and visitors will undergo a temperature check at arrival. No more than 3 people at a time in a taxi/ride-share including the driver. All passengers wearing masks. Buses should operate with no more than 30% customer's capacity per bus.</div>
      <div class="cell"><span class="icon" role="img" aria-label="Coffee shop icon"></span>Coffee &amp; restaurants can reopen but must operate at 30% capacity as well and comply with social distancing. Clients must wear as much as possible their masks if they are not consuming food/coffee. Clients should avoid to talking to each other with masks off.</div>
      <div class="cell"><span class="icon" role="img" aria-label="Large events closed icon"></span>Large scale events (cinema, theaters, sport, business conferences, etc.) should remain closed or operate without spectators. Sport events can resume but without spectators. Athletes and the staff surrounding them should be tested, disinfectants should be available and masks used as much as reasonably possible.</div>
    </div>
  </section>

  <section class="stage stage--two">
    <div class="stage__badge-wrap"><span class="badge stage__badge">STAGE : 2</span></div>
    <p class="stage__lead">To enter stage 2 of the Covid-19 Exit Strategy, compliance to the general requirements is compulsory, additional to a successful Stage 1 outcome. The Effective Reproduction Number (Rt) for Stage 2 must be less than 0.5 and the death rate stabilized at less than 1.5%.</p>
    <p class="stage__seq">The economy and social activities can resume in this sequence:</p>
    <div class="grid">
      <div class="cell"><span class="icon" role="img" aria-label="Elderly person icon"></span>Elderly (60+ years old) and vulnerable individuals should continue to self-isolate as much as possible.</div>
      <div class="cell"><span class="icon" role="img" aria-label="No gatherings icon"></span>No more than 10 people maximum gathering at a time in public areas and at work.</div>
      <div class="cell"><span class="icon" role="img" aria-label="Work from home icon"></span>Work from home should if possible or for jobs that do not have to be necessarily in an office setup.</div>
      <div class="cell"><span class="icon" role="img" aria-label="Social distancing icon"></span>Social distancing can be relaxed. However people should continue to wear masks and use disinfectants.</div>
      <div class="cell"><span class="icon" role="img" aria-label="Travel icon"></span>Travel can resume between cities and regions. The same containment restrictions should apply to any existing hotspot.</div>
      <div class="cell"><span class="icon" role="img" aria-label="Hospital icon"></span>Elective surgeries can resume in hospitals and clinics that are equipped to comply with all general requirements.</div>
      <div class="cell"><span class="icon" role="img" aria-label="Large business icon"></span>Large businesses (300 people and more, manufacturing, services, etc.) will continue to operate. Common areas should open but social distancing should remain (cafeteria, restaurant, gym, meeting rooms of no more than 10 people).</div>
      <div class="cell"><span class="icon" role="img" aria-label="Small business icon"></span>Small businesses (300 people and less) will continue to operate with the same conditions as large businesses.</div>
      <div class="cell"><span class="icon" role="img" aria-label="Shop icon"></span>Commercial shops will continue to be open and can operate at 50% capacity. Wear of masks should continue.</div>
      <div class="cell"><span class="icon" role="img" aria-label="Pharmacy icon"></span>Commercial shops will continue to be open and can operate at 50% capacity. Wear of masks should continue.</div>
      <div class="cell"><span class="icon" role="img" aria-label="Religious site icon"></span>Religious sites can operate with a maximum capacity of 50%. Social distancing and wearing masks should be enforced. Sites should continue to check body temperature of everyone accessing the site and provide disinfectant at entry.</div>
      <div class="cell"><span class="icon" role="img" aria-label="Hotel icon"></span>Hotels &amp; tourism (museums, etc.) can operate at 50% capacity. All common areas (restaurants, gyms, swimming pools, conference rooms, etc.) could reopen. Gatherings are limited to 10 people or less and can be expanded with social distancing and wearing protective masks.</div>
      <div class="cell"><span class="icon" role="img" aria-label="Coffee shop icon"></span>Coffee &amp; restaurants can operate at 50% capacity and continue comply with social distancing. Clients must wear as much as possible their masks if they are not consuming food/coffee.</div>
      <div class="cell"><span class="icon" role="img" aria-label="School icon"></span>Schools can reopen in parallel with on-line education. Social distancing and re-arranging school seating to prevent the spread of infection is mandatory.</div>
      <div class="cell"><span class="icon" role="img" aria-label="Large events icon"></span>Large scale events (cinema, theaters, sport, business conferences, etc.) could resume under strict social distancing. People should wear masks.</div>
      <div class="cell cell--wide"><span class="icon" role="img" aria-label="Transport icon"></span>Transportation (buses, taxis, and airlines) will continue to operate. Still no air travels permitted in and out of Covid-19 known hotspots, locally or internationally. Entry to country should be relaxed but remain controlled. Airports should continue to use thermo cameras to monitor passenger's temperature at landing. Airports should be equipped to test for Covid-19 if necessary. Transportation by taxi/ride-share continues, however, passengers wear masks. Buses could operate with 50% capacity per bus.</div>
    </div>
  </section>

  <section class="stage stage--three">
    <div class="stage__badge-wrap"><span class="badge stage__badge">STAGE : 3</span></div>
    <p class="stage__lead">To enter stage 3 of the Covid-19 Exit Strategy, compliance to the general requirements is compulsory, additional to a successful Stage 2 outcome. The Effective Reproduction Number (Rt) for Stage 3 must be less than 0.3 and the death rate stabilized at less than 1%.</p>
    <p class="stage__seq">The economy and social activities can resume in this sequence:</p>
    <div class="grid">
      <div class="cell"><span class="icon" role="img" aria-label="Elderly person icon"></span>Elderly (60+ years old) and vulnerable individuals may resume all previously exercised activities without restrictions.</div>
      <div class="cell"><span class="icon" role="img" aria-label="Gatherings icon"></span>Restrictions as to the number of people gathering together can be lifted. Social distancing can be relaxed. However, wear of masks may continue.</div>
      <div class="cell"><span class="icon" role="img" aria-label="Travel icon"></span>Travel can resume between cities and regions and out of country travel. The same containment restrictions as Stage 1 and 2 would continue to apply to any existing hotspot.</div>
      <div class="cell"><span class="icon" role="img" aria-label="Hospital icon"></span>All hospital and clinic surgeries can resume in hospitals in compliance with standard hospital and health care procedures.</div>
      <div class="cell"><span class="icon" role="img" aria-label="Large business icon"></span>Large businesses (300 people and more, manufacturing, services, etc.) will resume normal business practices. Wear of masks is recommended but not mandatory.</div>
      <div class="cell"><span class="icon" role="img" aria-label="Small business icon"></span>Small businesses (300 people and less) will operate with the same conditions as large businesses.</div>
      <div class="cell"><span class="icon" role="img" aria-label="Shop icon"></span>Commercial shops can operate on a normal mode - previous to covid-19. Wear of masks could be recommended in certain areas.</div>
      <div class="cell"><span class="icon" role="img" aria-label="Pharmacy icon"></span>Pharmacies can operate at a normal state.</div>
      <div class="cell"><span class="icon" role="img" aria-label="Religious site icon"></span>Religious sites can operate normally. Wear of masks should be elective.</div>
      <div class="cell"><span class="icon" role="img" aria-label="Hotel icon"></span>Hotels &amp; tourism (museums, etc.) can operate at 100% capacity including all common areas.</div>
      <div class="cell"><span class="icon" role="img" aria-label="Coffee shop icon"></span>Coffee &amp; restaurants can resume normal operations. Clients may wear masks for personal protection if they wish to.</div>
      <div class="cell"><span class="icon" role="img" aria-label="School icon"></span>Schools can resume normal operations. Re-arranging school seating should continue until a vaccine is found.</div>
      <div class="cell"><span class="icon" role="img" aria-label="Large events icon"></span>Large scale events (cinema, theaters, sport, business conferences, etc.) could resume under moderate social distancing. People may elect to wear masks.</div>
      <div class="cell cell--span2"><span class="icon" role="img" aria-label="Transport icon"></span>Transportation (buses, taxis, and airlines) will operate at a normal capacity. Still no air travels permitted in and out of Covid-19 known hotspots, locally or internationally. Entry to country should be relaxed and operate normally. Airports should continue to use thermo cameras to monitor passenger's temperature at landing. Airports should be equipped to test for Covid-19 if necessary. Transportation by taxi/ride-share and buses will resume on a normal mode. Wear of masks is elective.</div>
    </div>
  </section>

  <footer class="footer">
    <div class="footer__org"><span class="footer__org-mark"></span>Civic Health Office</div>
    <div class="footer__block"><strong>#STAYSAFEATHOME</strong>Don't have to go outside? Please stay at home!</div>
    <div class="footer__block"><strong>FOR INFORMATION</strong>&#9742; 8000-1234 &nbsp; www.exitplan-info.org</div>
  </footer>

</main>
</body>
</html>
```